Building company buisness cards

We are looking for a sharp modern new look for our business cards.
We are a New Zealand based company that specialises in house and land packages.
We have attached a photo of the current logo and would like to see if it can be improved somehow if needed.
We are open to any colours but we have chosen green at this stage.
Feel free to change the font and make the logo smarter looking.
Play with the colours and see what looks best.

We want a card that looks so good know one will want to throw it away!

Target Market(s)

Home buyers

Industry/Entity Type

Building

Contact Information for Business Card

Derek Tolvane
0217394062
dtolvane@quillmarkhomesteads.co.nz
quillmarkhomesteads.co.nz

Font styles to use
Serif
Sans Serif

Colors

Designer to choose colors to be used in the design.

Requirements
Must have
• Logo and company name on one side, details on the other side
Nice to have
• Color codes for the original green are HEX #4a8028, RGB(74,128,40), CMYK(42,0,69,50)
• Round corners, Raised and/or spot UV

```html
<!DOCTYPE html>
<html lang="en">
<head>
<meta charset="utf-8">
<title>Quillmark Homesteads – Business Cards</title>
<link href="https://fonts.googleapis.com/css2?family=Nunito:wght@900&family=Source+Sans+3:wght@400&family=Arimo:wght@700&display=swap" rel="stylesheet">
<style>
  :root {
    --green: #4a8028;
    --green-light: #5c9a34;
    --grey: #6d6d6d;
    --ink: #2a2a2a;
    --paper: #ffffff;
    --backdrop: #1e1e1e;
  }
  * { margin: 0; padding: 0; box-sizing: border-box; }
  html, body {
    width: 1200px; height: 960px; overflow: hidden;
    background: var(--backdrop);
  }
  .stage { position: relative; width: 1200px; height: 960px; }

  .card {
    position: absolute;
    background: var(--paper);
    border-radius: 10px;
    overflow: hidden;
  }

  /* Brand side */
  .card--brand { left: 580px; top: 110px; width: 560px; height: 320px; }
  .brand-block {
    position: absolute; right: 36px; bottom: 44px;
    text-align: right;
  }
  .wordmark {
    display: flex; align-items: center; justify-content: flex-end; gap: 12px;
    font-family: "Nunito", sans-serif; font-weight: 900;
    color: var(--green); line-height: 0.95;
  }
  .wordmark__dot {
    width: 16px; height: 16px; border-radius: 50%; background: var(--green);
    flex: none;
  }
  .wordmark__text { text-align: right; }
  .wordmark--large .wordmark__text { font-size: 38px; }
  .brand-rule {
    width: 150px; height: 2px; background: var(--green);
    margin: 12px 70px 10px auto;
  }
  .brand-web {
    font-family: "Source Sans 3", sans-serif; font-size: 17px; color: var(--ink);
  }
  .brand-web span { color: var(--green); }

  /* Details side */
  .card--details { left: 120px; top: 470px; width: 560px; height: 320px; }
  .details-head { position: absolute; left: 44px; top: 28px; }
  .wordmark--small { justify-content: flex-start; }
  .wordmark--small .wordmark__text { font-size: 24px; text-align: left; }
  .wordmark--small .wordmark__dot { width: 12px; height: 12px; }
  .details-head .brand-rule { margin: 8px 0 0 60px; width: 120px; height: 1.5px; }

  .contact-list {
    position: absolute; left: 44px; top: 106px; list-style: none;
    font-family: "Source Sans 3", sans-serif; font-size: 15px; color: var(--ink);
  }
  .contact-list li { display: flex; align-items: center; gap: 8px; height: 22px; }
  .contact-list svg { width: 12px; height: 12px; flex: none; }

  .swoosh { position: absolute; left: 0; top: 0; width: 560px; height: 320px; }
  .holder-name {
    position: absolute; right: 60px; bottom: 26px;
    font-family: "Arimo", sans-serif; font-weight: 700; font-size: 24px;
    color: var(--paper); letter-spacing: 0.3px;
  }
</style>
</head>
<body>
<main class="stage">

  <section class="card card--brand" aria-label="Card front">
    <div class="brand-block">
      <div class="wordmark wordmark--large">
        <span class="wordmark__dot"></span>
        <span class="wordmark__text">quillmark<br>homesteads.</span>
      </div>
      <div class="brand-rule"></div>
      <p class="brand-web">www.<span>quillmarkhomesteads</span>.co.nz</p>
    </div>
  </section>

  <section class="card card--details" aria-label="Card back">
    <svg class="swoosh" viewBox="0 0 560 320" preserveAspectRatio="none" aria-hidden="true">
      <path d="M0 218 C150 252 320 268 560 250 L560 320 L0 320 Z" fill="var(--green)"/>
      <path d="M0 206 C160 242 330 258 560 238" fill="none" stroke="var(--grey)" stroke-width="4"/>
      <path d="M0 198 C165 236 335 252 560 230" fill="none" stroke="var(--green-light)" stroke-width="2"/>
      <path d="M0 192 C170 230 340 246 560 222" fill="none" stroke="var(--grey)" stroke-width="1.2"/>
    </svg>

    <header class="details-head">
      <div class="wordmark wordmark--small">
        <span class="wordmark__dot"></span>
        <span class="wordmark__text">quillmark<br>homesteads.</span>
      </div>
      <div class="brand-rule"></div>
    </header>

    <ul class="contact-list">
      <li>
        <svg viewBox="0 0 12 12"><path d="M3 1 L5 3.5 L4 5 C5 7 5.5 7.5 7 8 L8.5 7 L11 9 L9.5 11 C5 11 1 7 1 2.5 Z" fill="var(--green)"/></svg>
        0217394062
      </li>
      <li>
        <svg viewBox="0 0 12 12"><rect x="1" y="2.5" width="10" height="7" rx="1" fill="var(--green)"/><path d="M1.5 3 L6 6.5 L10.5 3" fill="none" stroke="#fff" stroke-width="1"/></svg>
        dtolvane@quillmarkhomesteads.co.nz
      </li>
      <li>
        <svg viewBox="0 0 12 12"><circle cx="6" cy="6" r="5" fill="var(--green)"/><path d="M1 6 H11 M6 1 C3.5 3.5 3.5 8.5 6 11 M6 1 C8.5 3.5 8.5 8.5 6 11" fill="none" stroke="#fff" stroke-width="0.8"/></svg>
        www.quillmarkhomesteads.co.nz
      </li>
    </ul>

    <p class="holder-name">Derek Tolvane</p>
  </section>

</main>
</body>
</html>
```